Priority Goals poster for school year

We are an elementary school and the past two years have had you help us to design a "poster" that illustrates our goal of the coming year. I am attaching our last year's one, along with some photos of our (ver rough) thinking for next years. The priority goal at top remains the same. Can't wait to see your genius ideas! :)

Target Market(s)

Staff of an elementary school and parents to some (informative) extent as well.

Colors
296eb1
6094c6
fbed22
fbee3f

Requirements
Must have
• items from the white board picture we have attached

```html
<!DOCTYPE html>
<html lang="en">
<head>
<meta charset="utf-8">
<title>2021-2022 Priority Goals – Cedar Ridge Elementary School</title>
<link href="https://fonts.googleapis.com/css2?family=Montserrat:wght@600;700;800;900&family=Oswald:wght@500;600;700&family=Poppins:wght@400;500;600&display=swap" rel="stylesheet">
<style>
  :root {
    --backdrop: #66666a;
    --paper: #ffffff;
    --body-grey: #e6e9ef;
    --navy: #1e3270;
    --royal: #243f93;
    --brand-blue: #296eb1;
    --sky: #6094c6;
    --pale-blue: #8fb5df;
    --yellow: #fbed22;
    --gold: #e9b90a;
    --gold-mid: #f0c419;
    --gold-soft: #f5d43a;
    --gold-pale: #faeaa0;
    --ink: #1e3270;
  }
  * { box-sizing: border-box; margin: 0; padding: 0; }
  html, body { width: 1200px; height: 1200px; overflow: hidden; }
  body { background: var(--backdrop); position: relative; font-family: "Poppins", Arial, sans-serif; }

  .poster {
    position: absolute; left: 176px; top: 0;
    width: 848px; height: 1200px;
    background: var(--body-grey);
    overflow: hidden;
  }
  .poster-header { position: absolute; inset: 0 0 auto 0; height: 251px; background: var(--paper); }
  .poster-title {
    position: absolute; left: 28px; top: 20px;
    font-family: "Montserrat", Arial, sans-serif; font-weight: 800;
    font-size: 38px; letter-spacing: 0.2px; color: var(--navy);
  }
  .poster-title .year { color: var(--gold); }
  .mission-band {
    position: absolute; left: 0; top: 80px; width: 604px; height: 102px;
    background: var(--brand-blue);
    padding: 22px 0 0 46px;
    color: #fff; font-size: 18.5px; line-height: 1.38; font-weight: 500;
  }
  .school-name {
    position: absolute; right: 26px; top: 92px; width: 230px;
    display: flex; align-items: center; gap: 12px;
    font-family: "Montserrat", Arial, sans-serif; font-weight: 800;
    color: var(--navy); font-size: 21px; line-height: 1.12; text-transform: uppercase;
  }
  .school-name .dot { flex: none; width: 44px; height: 44px; border-radius: 50%; background: var(--gold); }

  .wheel { position: absolute; left: 0; top: 251px; width: 848px; height: 850px; }
  .wheel text { font-family: "Oswald", Arial, sans-serif; }
  .seg-label { font-family: "Montserrat", Arial, sans-serif !important; font-weight: 800; font-size: 14.5px; fill: var(--ink); }
  .seg-label.on-dark { fill: #fff; }
  .seg-note { font-family: "Poppins", Arial, sans-serif !important; font-size: 10.5px; fill: var(--ink); }
  .seg-note.on-dark { fill: #fff; }

  .footer-rule { position: absolute; left: 0; right: 0; top: 1101px; height: 9px; background: var(--yellow); }
  .poster-footer {
    position: absolute; left: 0; right: 0; bottom: 0; height: 90px;
    background: var(--navy); color: #fff;
    display: flex; align-items: center; justify-content: space-between;
    padding: 0 40px 0 50px;
    font-family: "Montserrat", Arial, sans-serif; font-weight: 700; font-size: 17px;
  }
  .contact-list { list-style: none; display: flex; flex-direction: column; gap: 4px; }
  .contact-list li { display: flex; align-items: center; gap: 9px; }
  .contact-list svg { width: 14px; height: 14px; flex: none; }
  .social-handle { display: flex; align-items: center; gap: 12px; font-size: 21px; }
  .social-handle .dot { width: 34px; height: 34px; border-radius: 50%; border: 2px solid #fff; }
</style>
</head>
<body>
<main class="poster">
  <header class="poster-header">
    <h1 class="poster-title"><span class="year">2021-2022</span> PRIORITY GOALS</h1>
    <p class="mission-band">We WILL accelerate the academic &amp; social/emotional<br>growth of the students we serve by:</p>
    <div class="school-name"><span class="dot"></span><span>Cedar Ridge Elementary School</span></div>
  </header>

  <svg class="wheel" viewBox="0 0 848 850" aria-labelledby="wheel-title">
    <title id="wheel-title">Foundational Promises wheel</title>
    <defs>
      <linearGradient id="ring-grad" x1="0" y1="0" x2="1" y2="0">
        <stop offset="0" stop-color="#7fb0e3"/>
        <stop offset="1" stop-color="#1f3f92"/>
      </linearGradient>
      <filter id="soft-shadow" x="-30%" y="-30%" width="160%" height="160%">
        <feDropShadow dx="0" dy="3" stdDeviation="4" flood-color="#1e3270" flood-opacity="0.25"/>
      </filter>
    </defs>

    <g transform="translate(424 425)">
      <circle class="outer-ring" r="392" fill="none" stroke="url(#ring-grad)" stroke-width="14"/>
      <circle r="383" fill="#fff"/>
      <path class="inner-ring" d="M91.1 -340 A352 352 0 1 1 -91.1 -340" fill="none" stroke="var(--sky)" stroke-width="5"/>

      <path d="M112.9 -310.2 A330 330 0 0 1 310.2 -112.9 L141 -51.3 A150 150 0 0 0 51.3 -141 Z" fill="var(--gold)"/>
      <path d="M310.2 -112.9 A330 330 0 0 1 310.2 112.9 L141 51.3 A150 150 0 0 0 141 -51.3 Z" fill="var(--gold-mid)"/>
      <path d="M310.2 112.9 A330 330 0 0 1 189.3 270.3 L86.1 122.9 A150 150 0 0 0 141 51.3 Z" fill="var(--gold-soft)"/>
      <path d="M189.3 270.3 A330 330 0 0 1 0 330 L0 150 A150 150 0 0 0 86.1 122.9 Z" fill="var(--gold-pale)"/>
      <path d="M0 330 A330 330 0 0 1 -212.1 252.8 L-96.4 114.9 A150 150 0 0 0 0 150 Z" fill="var(--pale-blue)"/>
      <path d="M-212.1 252.8 A330 330 0 0 1 -318.8 85.4 L-144.9 38.9 A150 150 0 0 0 -96.4 114.9 Z" fill="var(--brand-blue)"/>
      <path d="M-318.8 85.4 A330 330 0 0 1 -299.1 -139.5 L-135.9 -63.4 A150 150 0 0 0 -144.9 38.9 Z" fill="var(--royal)"/>
      <path d="M-299.1 -139.5 A330 330 0 0 1 -112.9 -310.2 L-51.3 -141 A150 150 0 0 0 -135.9 -63.4 Z" fill="var(--navy)"/>

      <text x="0" y="-262" text-anchor="middle" font-size="84" font-weight="700" fill="var(--gold)">4</text>
      <text x="0" y="-232" text-anchor="middle" font-size="21" font-weight="600" fill="var(--gold)">YEARS STRONG</text>
      <text x="0" y="-206" text-anchor="middle" font-size="21" font-weight="600" fill="var(--brand-blue)">BETTER</text>
      <text x="0" y="-180" text-anchor="middle" font-size="21" font-weight="600" fill="var(--brand-blue)">EVERYDAY!</text>
      <rect x="-28" y="-170" width="56" height="4" fill="var(--brand-blue)"/>

      <circle r="150" fill="#fff" filter="url(#soft-shadow)"/>
      <circle cx="0" cy="-52" r="44" fill="#dce8f5" role="img" aria-label="Heart-shaped handshake emblem"/>
      <text x="0" y="32" text-anchor="middle" font-size="38" font-weight="700" fill="var(--navy)">FOUNDATIONAL</text>
      <text x="0" y="76" text-anchor="middle" font-size="38" font-weight="700" fill="var(--navy)">PROMISES</text>

      <g text-anchor="middle">
        <text class="seg-label on-dark" x="-152" y="-180">VOICES OF ALL</text>
        <text class="seg-note on-dark" x="-150" y="-164">Who are we?</text>
        <text class="seg-note on-dark" x="-150" y="-151">Where are we going?</text>

        <text class="seg-label on-dark" x="-212" y="-26">BROADEN</text>
        <text class="seg-label on-dark" x="-212" y="-8">OUR LENS</text>

        <text class="seg-label on-dark" x="-180" y="92">SMALL</text>
        <text class="seg-label on-dark" x="-180" y="108">MEASURED</text>
        <text class="seg-label on-dark" x="-180" y="124">STEPS</text>
        <text class="seg-note on-dark" x="-180" y="139">Towards</text>
        <text class="seg-note on-dark" x="-180" y="152">Bigger Goal</text>

        <text class="seg-label on-dark" x="-82" y="196">BUILDS &amp; VALUE</text>
        <text class="seg-label on-dark" x="-82" y="212">PARTNERSHIPS</text>
        <text class="seg-note on-dark" x="-82" y="227">Connect, Celebrate, Strong,</text>
        <text class="seg-note on-dark" x="-82" y="240">Predictable, Laugh, Have Fun!</text>

        <text class="seg-label" x="88" y="196">COMMUNICATION,</text>
        <text class="seg-label" x="88" y="212">COMMUNICATION,</text>
        <text class="seg-label" x="88" y="228">COMMUNICATION!</text>
        <text class="seg-note" x="88" y="243">Expectations, Support</text>
        <text class="seg-note" x="88" y="256">For Clarity</text>

        <text class="seg-label" x="160" y="100">FOCUS</text>
        <text class="seg-note" x="160" y="116">Be intentional with</text>
        <text class="seg-note" x="160" y="129">your action</text>

        <text class="seg-label" x="205" y="-48">STAFF DOING</text>
        <text class="seg-label" x="205" y="-32">WHAT THEY</text>
        <text class="seg-label" x="205" y="-16">LOVE</text>
        <text class="seg-note" x="205" y="-1">Teaching kids</text>
        <text class="seg-note" x="205" y="12">for proven growth</text>

        <text class="seg-label" x="162" y="-190">MENTAL HEALTH</text>
        <text class="seg-label" x="162" y="-174">&amp; WELLNESS</text>
        <text class="seg-note" x="162" y="-159">For every person in our</text>
        <text class="seg-note" x="162" y="-146">community &amp; school</text>
      </g>

      <g class="badges">
        <g transform="translate(-215 -250)">
          <circle r="36" fill="#fff" filter="url(#soft-shadow)"/><circle r="29" fill="var(--navy)"/>
          <g fill="#fff"><circle cx="-9" cy="-8" r="4"/><circle cx="9" cy="-8" r="4"/><circle cx="0" cy="-4" r="4"/>
          <rect x="-13" y="-2" width="8" height="14" rx="3"/><rect x="5" y="-2" width="8" height="14" rx="3"/><rect x="-4" y="2" width="8" height="13" rx="3"/></g>
        </g>
        <g transform="translate(-302 -30)">
          <circle r="36" fill="#fff" filter="url(#soft-shadow)"/><circle r="29" fill="var(--royal)"/>
          <path d="M-15 0 Q0 -14 15 0 Q0 14 -15 0 Z" fill="none" stroke="#fff" stroke-width="2.5"/><circle r="5" fill="#fff"/>
        </g>
        <g transform="translate(-274 128)">
          <circle r="36" fill="#fff" filter="url(#soft-shadow)"/><circle r="29" fill="var(--brand-blue)"/>
          <g fill="#fff"><ellipse cx="-6" cy="-3" rx="4.5" ry="8"/><ellipse cx="6" cy="4" rx="4.5" ry="8"/></g>
        </g>
        <g transform="translate(-112 302)">
          <circle r="36" fill="#fff" filter="url(#soft-shadow)"/><circle r="29" fill="var(--pale-blue)"/>
          <g fill="#fff"><circle cx="-7" cy="-10" r="4"/><circle cx="7" cy="-10" r="4"/>
          <rect x="-11" y="-4" width="7" height="17" rx="3"/><rect x="4" y="-4" width="7" height="17" rx="3"/></g>
        </g>
        <g transform="translate(96 302)">
          <circle r="36" fill="#fff" filter="url(#soft-shadow)"/><circle r="29" fill="var(--gold-pale)"/>
          <g fill="none" stroke="var(--navy)" stroke-width="2"><rect x="-13" y="-12" width="11" height="8" rx="2"/><rect x="2" y="-12" width="11" height="8" rx="2"/>
          <circle cx="-7" cy="3" r="3"/><circle cx="7" cy="3" r="3"/><path d="M-13 14 Q-7 6 -1 14 M1 14 Q7 6 13 14"/></g>
        </g>
        <g transform="translate(247 175)">
          <circle r="36" fill="#fff" filter="url(#soft-shadow)"/><circle r="29" fill="var(--gold-soft)"/>
          <g fill="none" stroke="var(--navy)" stroke-width="2.2"><circle r="10"/><circle r="3.5"/><path d="M0 -16 V-10 M0 10 V16 M-16 0 H-10 M10 0 H16"/></g>
        </g>
        <g transform="translate(304 -30)">
          <circle r="36" fill="#fff" filter="url(#soft-shadow)"/><circle r="29" fill="var(--gold-mid)"/>
          <g fill="none" stroke="var(--navy)" stroke-width="2.2"><circle cy="-7" r="6"/><path d="M-13 14 Q0 -4 13 14"/><path d="M-3 5 l3 3 l3 -3"/></g>
        </g>
        <g transform="translate(189 -270)">
          <circle r="36" fill="#fff" filter="url(#soft-shadow)"/><circle r="29" fill="var(--gold)"/>
          <g fill="none" stroke="var(--navy)" stroke-width="2.2"><circle cy="-5" r="8"/><path d="M-16 4 Q-12 14 -4 14 M16 4 Q12 14 4 14"/></g>
        </g>
      </g>
    </g>
  </svg>

  <div class="footer-rule"></div>
  <footer class="poster-footer">
    <ul class="contact-list">
      <li><svg viewBox="0 0 14 14" aria-hidden="true"><path d="M7 0.5 A4.8 4.8 0 0 1 11.8 5.3 C11.8 8.6 7 13.5 7 13.5 C7 13.5 2.2 8.6 2.2 5.3 A4.8 4.8 0 0 1 7 0.5 Z" fill="var(--yellow)"/><circle cx="7" cy="5.3" r="1.8" fill="var(--navy)"/></svg>1180 Ridgeline Ave., Pine Hollow, WA 98100</li>
      <li><svg viewBox="0 0 14 14" aria-hidden="true"><path d="M3 1 L5.5 1 L6.5 4 L5 5.5 Q6.5 8.5 8.5 9 L10 7.5 L13 8.5 L13 11 Q13 13 11 13 Q1 12 1 3 Q1 1 3 1 Z" fill="var(--yellow)"/></svg>555-014-2200</li>
    </ul>
    <div class="social-handle"><span class="dot"></span><span>@cedarridgelearns</span></div>
  </footer>
</main>
</body>
</html>
```